Pella's Salon (Business Cards) Needed

I need a new business card for my hair salon based in Fairfax, VA called "Pella's Salon". I have been in business at the same location for the past 15 years, and have recently remodeled the place to be a little bit more upscale and modern. Previously, my clientele's were mostly men, but now I would like to attract more female clientele into my business. I would like the design to attract the female's attention with it's modern touch, flowery, freshness with just enough information and not too compact. Simple, clean and professional is the look.
Requirements
Must Have:
- The design should include:
Business name: Pella's Salon
Hairstylist/Owner Name: Pella Marsden
Phone Number: (555) 418-6307
Website: www.pellahairstudio.example
Address: 48153 Corwin Dale Lane
Fairfax, VA 20917
FRONT CARD should include:
- Logo (Business name)
- Slogan (Your beauty, our passion)
BACK CARD should include:
- Logo (Business name)
- Hairstyle name
- Phone number
- Website
- Address
Updates
Project Deadline Extended
Reason: There were some good submission for this project, but most of the submission were poorly designed, and did not have what I want. There isn't enough designs for me to choose from and not one of it stood out to me. I would like to extend it a bit longer to see if any other designer would step up to the plate, and deliver. Thank you.
Industry/Entity Type
Hair
Requirements
Must have
- The front side of the business card should only have the business name (Pella's Salon) and slogan, (Your beauty our passion) with a creative design.
The back side of the business card should have all the business information, and creative design that matches with the front, but not identical.
The first letter (V) in (Pella's) should have a flower design connected to it, which blends into the background design.
Nice to have
- Light color scheme.
Should not have
- The front, and back should not have the same design.
Do not include illustrations of a pair of scissors, combs or any objects in the design.
The design should not take the main focus from the business name and business information. It should blend well together... if that's possible.

```html
<!DOCTYPE html>
<html lang="en">
<head>
<meta charset="utf-8">
<title>Pella's Salon – Business Cards</title>
<link rel="stylesheet" href="https://fonts.googleapis.com/css2?family=Michroma&family=Exo+2:wght@400;500&display=swap">
<style>
  :root {
    --backdrop: #e2e2e2;
    --paper: #fbf9f8;
    --header: #f2e9e9;
    --blush: #e9c9cf;
    --blush-soft: #f6e4e7;
    --rule: #c9bcbe;
    --steel-light: #f4f0f0;
    --steel-dark: #cdbfc2;
    --text-dark: #2a2426;
    --text-mid: #6c5f62;
  }
  * { box-sizing: border-box; margin: 0; padding: 0; }
  html, body { width: 1200px; height: 949px; overflow: hidden; }
  body {
    background: var(--backdrop);
    font-family: "Exo 2", sans-serif;
    position: relative;
  }
  .card {
    position: absolute;
    top: 150px;
    width: 380px;
    height: 640px;
    border-radius: 26px;
    overflow: hidden;
    box-shadow: 0 10px 30px rgba(0,0,0,0.18);
  }
  .brand-name {
    position: relative;
    font-family: "Michroma", sans-serif;
    color: var(--text-dark);
    font-weight: 400;
    white-space: nowrap;
    text-align: center;
    font-size: 32px;
  }
  .flower-motif {
    position: absolute;
    width: 84px; height: 84px;
    border-radius: 50%;
    background: radial-gradient(circle, var(--blush) 0%, var(--blush-soft) 55%, rgba(246,228,231,0) 100%);
  }

  /* Front card */
  .card--front { left: 170px; background: var(--paper); }
  .front-title { position: absolute; top: 250px; left: 0; right: 0; }
  .card--front .flower-motif { top: -38px; left: 30px; }
  .slogan {
    position: absolute; top: 318px; left: 0; right: 0;
    text-align: center; color: var(--text-mid);
    font-size: 16px; letter-spacing: 2px; text-transform: uppercase;
  }
  .social-row {
    position: absolute; left: 0; right: 0; bottom: 40px;
    display: flex; justify-content: center; gap: 36px;
    color: var(--text-mid); font-size: 16px; letter-spacing: 0.5px;
  }
  .edge-band {
    position: absolute; left: 0; right: 0; bottom: 0; height: 16px;
    background: linear-gradient(var(--blush-soft), var(--blush));
  }

  /* Back card */
  .card--back { left: 650px; background: var(--paper); }
  .back-header {
    position: absolute; top: 0; left: 0; right: 0; height: 250px;
    background: var(--header);
  }
  .back-title { position: absolute; top: 92px; left: 0; right: 0; }
  .back-header .flower-motif { top: -34px; left: 28px; }
  .owner-line {
    position: absolute; top: 188px; left: 28px; right: 28px;
    display: flex; align-items: center; gap: 12px;
    color: var(--text-dark); font-size: 16px; letter-spacing: 1.5px;
  }
  .owner-line .role { margin-left: auto; letter-spacing: 1px; font-size: 16px; color: var(--text-mid); }
  .owner-line svg { width: 18px; height: 18px; fill: var(--text-dark); }

  .icon-column {
    position: absolute; top: 250px; bottom: 0; left: 0; width: 66px;
    background: linear-gradient(90deg, var(--steel-dark), var(--steel-light) 55%, var(--blush-soft));
  }
  .contact-list { position: absolute; top: 250px; bottom: 0; left: 0; right: 0; list-style: none; }
  .contact-item {
    height: 25%;
    display: flex; align-items: center;
    border-top: 1.5px solid var(--rule);
  }
  .contact-item:first-child { border-top: none; }
  .contact-icon { width: 66px; flex: none; display: flex; justify-content: center; }
  .contact-icon svg { width: 24px; height: 24px; fill: var(--text-dark); }
  .contact-text {
    padding-left: 20px; color: var(--text-dark);
    font-size: 17px; letter-spacing: 0.5px; line-height: 1.35;
  }
</style>
</head>
<body>

  <section class="card card--front" aria-label="Card front">
    <div class="front-title">
      <div class="flower-motif" role="img" aria-label="Soft flower motif joined to the first letter of the name"></div>
      <h1 class="brand-name">Pella's Salon</h1>
    </div>
    <p class="slogan">Your beauty, our passion</p>
    <div class="social-row">
      <span class="social-link">like</span>
      <span class="social-link">Folio</span>
      <span class="social-link">Chirp</span>
    </div>
    <div class="edge-band"></div>
  </section>

  <section class="card card--back" aria-label="Card back">
    <header class="back-header">
      <div class="back-title">
        <div class="flower-motif" role="img" aria-label="Soft flower motif joined to the first letter of the name"></div>
        <h2 class="brand-name">Pella's Salon</h2>
      </div>
      <div class="owner-line">
        <svg viewBox="0 0 20 20" aria-hidden="true"><circle cx="10" cy="6" r="4.5"/><path d="M1 20c0-5 4-8 9-8s9 3 9 8z"/></svg>
        <span class="owner-name">PELLA MARSDEN</span>
        <span class="role">founder</span>
      </div>
    </header>

    <div class="icon-column"></div>
    <ul class="contact-list">
      <li class="contact-item">
        <span class="contact-icon"><svg viewBox="0 0 24 24" aria-hidden="true"><path d="M6.6 10.8a15 15 0 0 0 6.6 6.6l2.2-2.2c.3-.3.7-.4 1-.2 1.1.4 2.3.6 3.6.6.6 0 1 .4 1 1V20c0 .6-.4 1-1 1A17 17 0 0 1 3 4c0-.6.4-1 1-1h3.5c.6 0 1 .4 1 1 0 1.3.2 2.5.6 3.6.1.3 0 .7-.2 1z"/></svg></span>
        <span class="contact-text">(555) 418-6307</span>
      </li>
      <li class="contact-item">
        <span class="contact-icon"><svg viewBox="0 0 24 24" aria-hidden="true"><path d="M2 5h20v14H2zm2 2v.5l8 5.5 8-5.5V7zm0 2.9V17h16V9.9l-8 5.5z"/></svg></span>
        <span class="contact-text">hello@pellahairstudio.example</span>
      </li>
      <li class="contact-item">
        <span class="contact-icon"><svg viewBox="0 0 24 24" aria-hidden="true"><path d="M12 2a10 10 0 1 0 0 20 10 10 0 0 0 0-20zm6.9 9h-3a15 15 0 0 0-1.3-6 8 8 0 0 1 4.3 6zM12 4.1c.9 1.3 1.7 3.8 1.9 6.9h-3.8c.2-3.1 1-5.6 1.9-6.9zM9.4 5a15 15 0 0 0-1.3 6h-3A8 8 0 0 1 9.4 5zm-4.3 8h3a15 15 0 0 0 1.3 6 8 8 0 0 1-4.3-6zm6.9 6.9c-.9-1.3-1.7-3.8-1.9-6.9h3.8c-.2 3.1-1 5.6-1.9 6.9zm2.6-.9a15 15 0 0 0 1.3-6h3a8 8 0 0 1-4.3 6z"/></svg></span>
        <span class="contact-text">www.pellahairstudio.example</span>
      </li>
      <li class="contact-item">
        <span class="contact-icon"><svg viewBox="0 0 24 24" aria-hidden="true"><path d="M12 2a7 7 0 0 0-7 7c0 5 7 13 7 13s7-8 7-13a7 7 0 0 0-7-7zm0 9.5a2.5 2.5 0 1 1 0-5 2.5 2.5 0 0 1 0 5z"/></svg></span>
        <span class="contact-text">48153 Corwin Dale Lane<br>Fairfax, VA 20917</span>
      </li>
    </ul>
  </section>

</body>
</html>
```